Morlavik APP redesign and color change

I am looking for a new design for my app. Please see the attached current design.

Currently, I have a functioning app but the colors and design are awful!
The logo is great but the rest of the app needs a refresh.
(Logo hi res not yet available but will upload soon.)
New colors or anything that is cutting edge.

Basically: It is a secure social media app within a school system where the teachers, students and parents can text, exchange photos, plan curriculum, etc.

I NEED ONLY landing page with a new look!
Looking for one distinct design for the landing page with new look.
The developer will apply this one design towards the rest of the pages/app screens.

Because part of the social media I need the feel and look of what is now the trend. Something that will attract and keep the client(s) interested. I am really leaving all the creative work to the designer and open to any suggestions.

Target Market(s)

Schools, community, teachers, students, colleges, sport teams

Industry/Entity Type

Non Profit

Font styles to use
Serif
Sans Serif

Colors

Designer to choose colors to be used in the design.

Requirements
Must have
• Sharp, trendy, millennial feel
Nice to have
• Up to designer
Should not have
• Up to designer

```html
<!DOCTYPE html>
<html lang="en">
<head>
<meta charset="utf-8">
<title>Morlavik – Sign in</title>
<link rel="stylesheet" href="https://fonts.googleapis.com/css2?family=Lato:wght@400;700&family=Roboto:wght@400&display=swap">
<style>
  :root {
    --scene-light: #d9b55a;
    --scene-mid: #b08a32;
    --scene-dark: #6e5214;
    --card-bg: rgba(250, 244, 228, 0.9);
    --label: #b47b0b;
    --ink: #2b2b2b;
    --rule: #6f6a5e;
    --button: #b67c00;
    --white: #ffffff;
    --footer-top: #3c4500;
    --footer-bottom: #566500;
  }
  * { margin: 0; padding: 0; box-sizing: border-box; }
  html, body { width: 741px; height: 1200px; overflow: hidden; }
  body { font-family: "Lato", Arial, sans-serif; background: var(--footer-bottom); }

  .screen { position: relative; width: 741px; height: 1200px; overflow: hidden; }

  .scene {
    position: absolute; left: 0; top: 0; width: 741px; height: 1023px;
    background:
      radial-gradient(ellipse at 50% 35%, rgba(235, 205, 130, 0.55), transparent 60%),
      linear-gradient(180deg, var(--scene-dark) 0%, var(--scene-mid) 30%, var(--scene-light) 62%, var(--scene-mid) 100%);
  }

  .footer-band {
    position: absolute; left: 0; top: 1023px; width: 741px; height: 177px;
    background: linear-gradient(180deg, var(--footer-top), var(--footer-bottom));
  }

  .brand {
    position: absolute; left: 0; top: 455px; width: 741px;
    text-align: center; color: var(--white);
    font-family: "Lato", Arial, sans-serif; font-weight: 700;
    font-size: 33px; letter-spacing: 17px; padding-left: 17px;
  }

  .login-card {
    position: absolute; left: 93px; top: 653px; width: 556px; height: 317px;
    background: var(--card-bg);
  }
  .field { position: absolute; left: 61px; width: 434px; }
  .field-user { top: 61px; }
  .field-pass { top: 202px; }
  .field-label {
    display: block; font-size: 17px; letter-spacing: 1.8px;
    color: var(--label); text-transform: uppercase;
  }
  .field-value {
    display: block; margin-top: 14px;
    font-family: "Roboto", Arial, sans-serif; font-size: 24px; color: var(--ink);
  }
  .field-user .field-value { padding-bottom: 19px; border-bottom: 1.5px solid var(--rule); }
  .password-dots { display: flex; gap: 9px; margin-top: 26px; }
  .password-dots span { width: 8px; height: 8px; border-radius: 50%; background: var(--ink); }

  .submit-button {
    position: absolute; left: 93px; top: 970px; width: 556px; height: 106px;
    background: var(--button); border: 0; color: var(--white);
    font-family: "Lato", Arial, sans-serif; font-size: 23px;
    display: flex; align-items: center; justify-content: space-between;
    padding: 0 59px 0 61px; text-align: left;
  }

  .signup-prompt {
    position: absolute; left: 0; top: 1120px; width: 741px;
    text-align: center; color: var(--white); font-size: 18px;
  }
</style>
</head>
<body>
  <main class="screen">
    <div class="scene" role="img" aria-label="Warm-toned photo of a library desk with stacked books, coloured pencils in a cup, glasses and an open book before blurred bookshelves"></div>
    <div class="footer-band"></div>

    <h1 class="brand">MORLAVIK</h1>

    <form class="login-card">
      <div class="field field-user">
        <span class="field-label">Username</span>
        <span class="field-value">todd@klemo.io</span>
      </div>
      <div class="field field-pass">
        <span class="field-label">Password</span>
        <div class="password-dots" aria-label="Password hidden">
          <span></span><span></span><span></span><span></span><span></span><span></span><span></span><span></span>
        </div>
      </div>
    </form>

    <button class="submit-button" type="button">
      <span>Get Started</span>
      <svg width="14" height="18" viewBox="0 0 14 18" aria-hidden="true"><path d="M0 0 L13 9 L0 18 Z" fill="#000"/></svg>
    </button>

    <p class="signup-prompt">Not registered? Create Account</p>
  </main>
</body>
</html>
```